Innovative Media Company needs Web Design

We need a web design for a new multimedia product that we are launching to potential partners and investors. The initial website we are looking to launch consists of three pages:
1.) A home/feature set page
2.) An account landing page
3.) An about us page
We would like the style of our website to be VERY similar to the following site: http://www.brintaro.com/tundra.
We have worked a bit on this project with a previous designer but were not happy with the results. As a guideline, you may refer to their previous work and the Tundra 88 website.
We realize this prize is a bit low for this project. However, there is a great opportunity for follow-on work. We are hoping to make a long-term business relationship with a high quality web-developer.
Attached are the product logo and our previous designer's work. Please let me know if you have any questions.
Thank you.
All,
Thanks for your submissions. Please note that rather than have headers that state "Enhanced TV Functionality" and "Seamless Device Integration", I would like to see all features (the six or seven boxes) in the same section. Also, please revise your designs to have the following statement below the picture that stretches across the screen and above the feature descriptions:
"Available via apps for the television and mobile devices,
naLix technology integrates numerous media components to provide users with
enhanced TV functionality and seamless device integration for an unparalleled
personalized viewing experience."
Thanks you.

```html
<!DOCTYPE html>
<html lang="en">
<head>
<meta charset="utf-8">
<title>naLix – Next Generation Television</title>
<link href="https://fonts.googleapis.com/css2?family=Ubuntu:wght@300;400&family=Open+Sans:wght@400;600&display=swap" rel="stylesheet">
<style>
:root{
  --page:#ffffff;
  --ink:#3a3a3a;
  --ink-soft:#555555;
  --logo:#5a5a5a;
  --hero-top:#2a2a2a;
  --hero-bottom:#161616;
  --hero-text:#f2f2f2;
  --rule:#8a8a8a;
  --divider:#dddddd;
  --footer-top:#3a3a3a;
  --footer-bottom:#1e1e1e;
  --footer-bar:#1a1a1a;
  --footer-text:#e6e6e6;
}
*{box-sizing:border-box;margin:0;padding:0}
html,body{width:727px;height:1200px;overflow:hidden}
body{position:relative;background:var(--page);font-family:"Open Sans",Arial,sans-serif;color:var(--ink)}
.abs{position:absolute}

.topline{left:0;top:0;width:727px;height:3px;background:#d8d8d8}
.site-header{left:0;top:3px;width:727px;height:87px}
.brand{left:50px;top:26px;display:flex;align-items:center;gap:8px}
.brand-dot{width:14px;height:14px;border-radius:50%;background:var(--logo)}
.brand-name{font-family:"Ubuntu",Arial,sans-serif;font-weight:400;font-size:36px;color:var(--logo);letter-spacing:1px}
.main-nav{right:22px;top:41px;display:flex;font-family:"Ubuntu",Arial,sans-serif;font-size:12px;color:#333}
.main-nav a{color:inherit;text-decoration:none;padding:0 14px;border-left:1px solid #cfcfcf;line-height:20px}
.main-nav a:first-child{border-left:none}

.hero{left:0;top:90px;width:727px;height:321px;background:radial-gradient(ellipse at 40% 40%,#323232 0%,var(--hero-top) 45%,var(--hero-bottom) 100%)}
.hero-tv{left:52px;top:47px;width:316px;height:218px;border-radius:4px;background:linear-gradient(160deg,#4e5a48,#7d8a6e 40%,#3b4434)}
.hero-copy{left:449px;top:84px;color:var(--hero-text);font-family:"Ubuntu",Arial,sans-serif;font-weight:300}
.hero-kicker{font-size:25px;line-height:28px}
.hero-title{font-size:34px;line-height:33px}
.hero-btn{left:453px;top:186px;width:82px;height:25px;border-radius:3px;background:linear-gradient(#fdfdfd,#d9d9d9);font-family:"Ubuntu",Arial,sans-serif;font-size:13px;color:#333;display:flex;align-items:center;justify-content:center;gap:4px}
.hero-arrows{left:655px;top:285px}

.intro-title{left:21px;top:434px;font-family:"Ubuntu",Arial,sans-serif;font-weight:300;font-size:26px;color:#333}
.intro-text{left:22px;top:474px;width:680px;font-size:7.6px;line-height:12.4px;color:var(--ink)}
.rule{left:81px;width:567px;border-top:1px dotted var(--rule)}

.feature{width:215px}
.feature h2{font-family:"Ubuntu",Arial,sans-serif;font-weight:300;font-size:17.5px;color:#333;height:32px}
.feature-media{height:120px;margin-bottom:10px;display:flex;align-items:flex-start}
.media-tv{width:172px;height:115px;border-radius:3px;background:linear-gradient(#7aa7d8 0%,#b9d3ee 45%,#c9442f 70%,#3f6a22 100%)}
.media-devices{width:148px;height:120px;border-radius:6px;background:linear-gradient(135deg,#2b2b2b,#5a5a5a 60%,#1f1f1f)}
.media-tablet{width:180px;height:100px;margin-top:2px;border-radius:4px;background:linear-gradient(160deg,#dfe3e8,#1c4e8c 45%,#0e2d57 80%,#b8bcc2)}
.feature p{font-size:7.6px;line-height:12.9px;color:var(--ink)}
.read-more{margin-top:10px;font-family:"Ubuntu",Arial,sans-serif;font-size:10.5px;color:#444;display:flex;align-items:center;gap:3px}
.divider{width:1px;height:110px;background:var(--divider)}

.site-footer{left:0;top:1073px;width:727px;height:99px;background:linear-gradient(var(--footer-top),var(--footer-bottom))}
.footer-nav{left:26px;top:14px;display:flex;gap:24px;font-size:8px;color:var(--footer-text)}
.footer-brand{left:22px;top:48px;font-family:"Ubuntu",Arial,sans-serif;font-size:13px;color:#8a8a8a}
.footer-contact{right:23px;top:10px;text-align:right;font-size:8px;line-height:19.5px;color:var(--footer-text)}
.footer-bar{left:0;top:1172px;width:727px;height:28px;background:var(--footer-bar);border-top:1px solid #333}
.copyright{left:20px;top:8px;font-size:8px;color:var(--footer-text)}
</style>
</head>
<body>
<div class="abs topline"></div>
<header class="abs site-header">
  <div class="abs brand"><span class="brand-dot"></span><span class="brand-name">naLix</span></div>
  <nav class="abs main-nav"><a href="#">Home</a><a href="#">Account Page</a><a href="#">About Us</a></nav>
</header>

<section class="abs hero">
  <div class="abs hero-tv" role="img" aria-label="Flat-screen television showing a sunlit forest stream"></div>
  <div class="abs hero-copy">
    <div class="hero-kicker">Step into the</div>
    <div class="hero-title">Next Generation<br>of television</div>
  </div>
  <a class="abs hero-btn">learn more
    <svg width="6" height="9" viewBox="0 0 6 9"><path d="M1 1l3.5 3.5L1 8" fill="none" stroke="#333" stroke-width="1.2"/></svg></a>
  <svg class="abs hero-arrows" width="34" height="22" viewBox="0 0 34 22">
    <path d="M10 2L2 11l8 9" fill="none" stroke="#e0e0e0" stroke-width="1.4"/>
    <path d="M24 2l8 9-8 9" fill="none" stroke="#e0e0e0" stroke-width="1.4"/>
  </svg>
</section>

<h1 class="abs intro-title">Get the next generation television now !</h1>
<p class="abs intro-text">E-Commerce is a major progress in technology that has changed the way in which the customers now purchase information, products and the services. It's the new way of providing an opportunity to make your products and services avaialable in the global market 24 hours a day through Internet&nbsp; Brightwave eSolutions is specialized in handling advanced web projects and the ongoing projects that require permanent maintenance and support .We like challenges and do complete these challenge with expertise we like solving questions that arises in such projects as these helps us to grow also.</p>

<div class="abs rule" style="top:544px"></div>

<article class="abs feature" style="left:22px;top:562px">
  <h2>TV Functionality</h2>
  <div class="feature-media"><div class="media-tv" role="img" aria-label="Television showing a field of tulips and a windmill"></div></div>
  <p>Brightwave eSolutions is specialized in handling advanced web projects and the ongoing projects that require permanent maintenance and support .We like challenges and do complete these challenge with expertise</p>
  <div class="read-more">READ MORE <svg width="5" height="8" viewBox="0 0 5 8"><path d="M1 1l3 3-3 3" fill="none" stroke="#444"/></svg></div>
</article>
<div class="abs divider" style="left:244px;top:566px"></div>
<article class="abs feature" style="left:261px;top:562px">
  <h2>Device Integration</h2>
  <div class="feature-media"><div class="media-devices" role="img" aria-label="Tablet and smartphones showing a media app"></div></div>
  <p>Brightwave eSolutions is specialized in handling advanced web projects and the ongoing projects that require permanent maintenance and support .We like challenges and do complete these challenge with expertise</p>
  <div class="read-more">READ MORE <svg width="5" height="8" viewBox="0 0 5 8"><path d="M1 1l3 3-3 3" fill="none" stroke="#444"/></svg></div>
</article>
<div class="abs divider" style="left:484px;top:566px"></div>
<article class="abs feature" style="left:505px;top:562px">
  <h2>Next Level product</h2>
  <div class="feature-media"><div class="media-tablet" role="img" aria-label="Tablet with stylus"></div></div>
  <p>Brightwave eSolutions is specialized in handling advanced web projects and the ongoing projects that require permanent maintenance and support .We like challenges and do complete these challenge with expertise</p>
  <div class="read-more">READ MORE <svg width="5" height="8" viewBox="0 0 5 8"><path d="M1 1l3 3-3 3" fill="none" stroke="#444"/></svg></div>
</article>

<div class="abs rule" style="top:809px"></div>

<article class="abs feature" style="left:22px;top:829px">
  <h2>TV Functionality</h2>
  <div class="feature-media"><div class="media-tv" role="img" aria-label="Television showing a field of tulips and a windmill"></div></div>
  <p>Brightwave eSolutions is specialized in handling advanced web projects and the ongoing projects that require permanent maintenance and support .We like challenges and do complete these challenge with expertise</p>
  <div class="read-more">READ MORE <svg width="5" height="8" viewBox="0 0 5 8"><path d="M1 1l3 3-3 3" fill="none" stroke="#444"/></svg></div>
</article>
<div class="abs divider" style="left:244px;top:833px"></div>
<article class="abs feature" style="left:261px;top:829px">
  <h2>Device Integration</h2>
  <div class="feature-media"><div class="media-devices" role="img" aria-label="Tablet and smartphones showing a media app"></div></div>
  <p>Brightwave eSolutions is specialized in handling advanced web projects and the ongoing projects that require permanent maintenance and support .We like challenges and do complete these challenge with expertise</p>
  <div class="read-more">READ MORE <svg width="5" height="8" viewBox="0 0 5 8"><path d="M1 1l3 3-3 3" fill="none" stroke="#444"/></svg></div>
</article>
<div class="abs divider" style="left:484px;top:833px"></div>
<article class="abs feature" style="left:505px;top:829px">
  <h2>Next Level product</h2>
  <div class="feature-media"><div class="media-tablet" role="img" aria-label="Tablet with stylus"></div></div>
  <p>Brightwave eSolutions is specialized in handling advanced web projects and the ongoing projects that require permanent maintenance and support .We like challenges and do complete these challenge with expertise</p>
  <div class="read-more">READ MORE <svg width="5" height="8" viewBox="0 0 5 8"><path d="M1 1l3 3-3 3" fill="none" stroke="#444"/></svg></div>
</article>

<div class="abs rule" style="top:1072px"></div>

<footer class="abs site-footer">
  <nav class="abs footer-nav"><span>Home</span><span>Account Page</span><span>About Us</span><span>Products</span><span>Contact Us</span></nav>
  <div class="abs footer-brand">naLix</div>
  <address class="abs footer-contact" style="font-style:normal">Address : XYZ Lorem Ipsum,<br>dummy text of the printing<br>industry.<br>Ph: 014 736 2091</address>
</footer>
<div class="abs footer-bar"><div class="abs copyright">© 2012 Company Name &nbsp;|&nbsp; All right reserved</div></div>
</body>
</html>
```